VENTURE CAPITAL GROUP BUSINESS CARD DESIGN

Venture Capital Group based in SF looking for a bold business card design. No trendy colour explosion, 3D effects etc. Just "simple" optical effects. Works on your brain, keeps your eye focused and sticks to your mind.
Target Market(s)
Technology startups
Industry/Entity Type
Venture Capital
Contact Information for Business Card
DESMOND WHITLAKE
MANAGING PARTNER
187 FENWORTH ST SAN FRANCISCO, CA 94187
415.555.0142 O
415.555.0147 F
415.555.0193 C
desmond@veldtmoorcapital.ventures

```html
<!DOCTYPE html>
<html lang="en">
<head>
<meta charset="utf-8">
<title>Veldtmoor Capital Group – Business Card</title>
<link href="https://fonts.googleapis.com/css2?family=Lustria&family=Saira+Condensed:wght@600&display=swap" rel="stylesheet">
<style>
  :root {
    --bg: #a9a6a7;
    --green-light: #5bbb51;
    --green-mid: #2f9a45;
    --green-dark: #17663a;
    --green-brand: #1f8a3e;
    --text-gray: #555555;
    --paper: #fbfbfb;
    --silver: #b4b4b6;
    --circle-light: #e8e8e8;
  }
  * { margin: 0; padding: 0; box-sizing: border-box; }
  html, body { width: 1200px; height: 1200px; overflow: hidden; }
  body {
    background: var(--bg);
    font-family: "Lustria", Georgia, serif;
    position: relative;
  }
  .card {
    position: absolute;
    left: 242px;
    width: 716px;
    height: 420px;
    overflow: hidden;
  }
  /* Front */
  .card--front {
    top: 117px;
    background: linear-gradient(180deg, var(--green-light) 0%, var(--green-mid) 55%, #1f7e3c 100%);
  }
  .front-mark {
    position: absolute;
    left: 50%;
    top: 92px;
    width: 150px;
    height: 150px;
    margin-left: -75px;
    border-radius: 50%;
    background: #2e9b49;
  }
  .front-name {
    position: absolute;
    left: 0;
    right: 0;
    top: 280px;
    text-align: center;
    color: #ffffff;
    font-size: 30px;
    letter-spacing: 3px;
  }
  /* Back */
  .card--back {
    top: 644px;
    background: var(--paper);
  }
  .back-mark {
    position: absolute;
    left: 42px;
    top: 44px;
    width: 92px;
    height: 92px;
    border-radius: 50%;
    background: var(--circle-light);
  }
  .back-name {
    position: absolute;
    left: 168px;
    top: 74px;
    color: var(--green-brand);
    font-size: 28px;
    letter-spacing: 2px;
  }
  .contact-list {
    position: absolute;
    left: 48px;
    top: 176px;
    list-style: none;
    color: var(--text-gray);
    font-size: 17px;
    line-height: 25px;
  }
  .contact-list li { display: flex; align-items: center; }
  .icon { width: 18px; height: 18px; margin-right: 17px; flex: none; fill: var(--green-brand); }
  .icon--inline { margin: 0 10px 0 12px; }
  .address { margin-top: 8px; }
  .wave { position: absolute; left: 0; top: 0; width: 716px; height: 420px; }
  .person {
    position: absolute;
    right: 30px;
    top: 322px;
    text-align: right;
    color: #ffffff;
  }
  .person-name {
    font-family: "Saira Condensed", "Arial Narrow", sans-serif;
    font-weight: 600;
    font-size: 26px;
    line-height: 30px;
  }
  .person-title { font-size: 16px; line-height: 22px; }
</style>
</head>
<body>

<section class="card card--front">
  <div class="front-mark"></div>
  <div class="front-name">VELDTMOOR CAPITAL GROUP</div>
</section>

<section class="card card--back">
  <svg class="wave" viewBox="0 0 804 469" preserveAspectRatio="none" aria-hidden="true">
    <defs>
      <linearGradient id="bandGreen" x1="0" y1="0" x2="1" y2="0">
        <stop offset="0" stop-color="#3fae49"/>
        <stop offset="0.55" stop-color="#238a42"/>
        <stop offset="1" stop-color="#17663a"/>
      </linearGradient>
      <linearGradient id="bandSilver" x1="0" y1="0" x2="1" y2="0">
        <stop offset="0" stop-color="#c9c9cb"/>
        <stop offset="0.5" stop-color="#8f8f92"/>
        <stop offset="1" stop-color="#b9b9bb"/>
      </linearGradient>
    </defs>
    <path d="M0,365 C150,405 330,430 520,330 C640,265 730,218 804,218 L804,238 C730,242 650,275 560,330 C430,410 240,435 0,418 Z" fill="url(#bandSilver)"/>
    <path d="M0,432 C240,452 430,425 570,345 C670,287 740,262 804,258 L804,469 L0,469 Z" fill="url(#bandGreen)"/>
  </svg>

  <div class="back-mark"></div>
  <div class="back-name">VELDTMOOR CAPITAL GROUP</div>

  <ul class="contact-list">
    <li>
      <svg class="icon" viewBox="0 0 20 20" aria-hidden="true"><path d="M2 6c0-2 3-3 8-3s8 1 8 3v2h-4V6H6v2H2z M4 9h12l2 8H2z"/></svg>
      415.555.0142
    </li>
    <li>
      <svg class="icon" viewBox="0 0 20 20" aria-hidden="true"><path d="M5 2h10v5H5z M2 8h16v7h-3v3H5v-3H2z M7 13v3h6v-3z"/></svg>
      415.555.0147
      <svg class="icon icon--inline" viewBox="0 0 20 20" aria-hidden="true"><path d="M5 1h10v18H5z M7 3v12h6V3z"/></svg>
      415.555.0193
    </li>
    <li>
      <svg class="icon" viewBox="0 0 20 20" aria-hidden="true"><path d="M1 4h18v12H1z M3 6l7 5 7-5v-0.5H3z"/></svg>
      desmond@veldtmoorcapital.ventures
    </li>
    <li>
      <svg class="icon" viewBox="0 0 20 20" aria-hidden="true"><path d="M10 1a9 9 0 1 0 0.01 0z M10 3c-1.5 2-2 4-2 7s0.5 5 2 7c1.5-2 2-4 2-7s-0.5-5-2-7z M3 9h14v2H3z" fill-rule="evenodd"/></svg>
      veldtmoorcapital.ventures
    </li>
    <li class="address">187 Fenworth St San Francisco, CA 94187</li>
  </ul>

  <div class="person">
    <div class="person-name">Desmond Whitlake</div>
    <div class="person-title">Managing Partner</div>
  </div>
</section>

</body>
</html>
```